Real Estate business card for me

Business card for a realtor. I have just a few "must haves"... so I am hoping to get some great ideas back without my telling you what I want.

I just want something cool, appealing to the eye, modern-ish while still looking clean and professional. I'm a young-spirited 40 yo man. I don't wan the business card of a 23 year old or a 63 year old! haha

Industry/Entity Type

Real Estate Agent

Contact Information for Business Card

Whatever Wexford Calloway logo you use, it should be true WC purple color. Outside of that, color scheme is open to ideas.

Requirements
Must have
• Must include:
• Wexford Calloway, Pemberly Estates
• Dale Fenwick
• REALTORĀ®
• 555.417.2093
• HomesWithDale@mailbox-demo.com
Nice to have
• Can include my picture, but it doesn't have to. I saw a card the other day with a house sketch on the backside saying "Your referrals are the sincerest compliment I can receive". That was cool. I also saw a card which one side was just a full frame picture of me, info on reverse side. I like all those ideas as well, but definitely open to ANYTHING cool, a little different, stands out from the monotony of business cards realtors are passing around. It needs to have a Wexford logo on it somewhere, but I don't want it huge or the focal point. Im selling me, not the franchise. You can literally google Wexford Calloway Home Services and find all of the logos. Any of the main stream ones will work. They are typically a dark purple or dark purple and cream.
Should not have
• I do not want a huge logo presence.

```html
<!DOCTYPE html>
<html lang="en">
<head>
<meta charset="utf-8">
<title>Dale Fenwick – Realtor Business Card</title>
<link rel="stylesheet" href="https://fonts.googleapis.com/css2?family=Cinzel:wght@400;600&family=Lato:wght@400&display=swap">
<style>
  :root {
    --stage: #e4e5e7;
    --front-top: #6e6f71;
    --front-bottom: #505153;
    --navy: #0b3467;
    --ink-light: #ffffff;
    --rule: rgba(255,255,255,0.85);
    --portrait-top: #6a6b6e;
    --portrait-mid: #4a4b4f;
    --portrait-bottom: #26272b;
  }
  * { box-sizing: border-box; margin: 0; padding: 0; }
  html, body { width: 1200px; height: 782px; overflow: hidden; background: var(--stage); }
  .stage {
    width: 1200px; height: 782px;
    display: flex; align-items: center; justify-content: center; gap: 44px;
  }
  .card {
    width: 520px; height: 297px; position: relative; overflow: hidden;
    box-shadow: 0 6px 18px rgba(0,0,0,0.18);
    color: var(--ink-light);
  }

  /* Front */
  .card--front { background: linear-gradient(160deg, var(--front-top), var(--front-bottom)); }
  .personal-mark {
    position: absolute; left: 26px; top: 70px; width: 214px;
    display: flex; flex-direction: column; align-items: center; text-align: center;
  }
  .personal-mark__square {
    width: 74px; height: 74px; border: 4px solid var(--ink-light);
    margin-bottom: 16px;
  }
  .personal-mark__name {
    font-family: "Cinzel", serif; font-weight: 400; font-size: 22px;
    letter-spacing: 0.5px; white-space: nowrap; line-height: 1.1;
  }
  .personal-mark__title {
    width: 100%;
    display: flex; align-items: center; gap: 8px; margin-top: 5px;
    font-family: "Lato", sans-serif; font-size: 7px; letter-spacing: 1px;
  }
  .personal-mark__title::before, .personal-mark__title::after {
    content: ""; flex: 1; height: 1px; background: var(--rule);
  }
  .portrait {
    position: absolute; right: 0; top: 0; width: 262px; height: 297px;
    background: linear-gradient(180deg, var(--portrait-top) 0%, var(--portrait-mid) 50%, var(--portrait-bottom) 100%);
  }

  /* Back */
  .card--back { background: var(--navy); }
  .contact {
    position: absolute; left: 0; right: 0; top: 40px;
    display: flex; flex-direction: column; align-items: center; text-align: center;
  }
  .contact__name {
    font-family: "Cinzel", serif; font-weight: 600; font-size: 27px; letter-spacing: 1px;
  }
  .contact__title { font-family: "Lato", sans-serif; font-size: 17px; margin-top: 2px; }
  .contact__rule { width: 300px; height: 1px; background: var(--rule); margin: 12px 0 10px; }
  .contact__line { font-family: "Lato", sans-serif; font-size: 19px; line-height: 1.3; }
  .brokerage {
    position: absolute; left: 104px; top: 216px;
    display: flex; align-items: center; gap: 8px;
  }
  .brokerage__dot { width: 13px; height: 13px; border-radius: 50%; border: 1px solid var(--ink-light); }
  .brokerage__name {
    font-family: "Cinzel", serif; font-weight: 400; font-size: 11px; line-height: 1.35;
    color: var(--ink-light);
  }
</style>
</head>
<body>
  <main class="stage">
    <section class="card card--front" aria-label="Card front">
      <div class="personal-mark">
        <div class="personal-mark__square"></div>
        <div class="personal-mark__name">Dale Fenwick</div>
        <div class="personal-mark__title">REALTOR®</div>
      </div>
      <div class="portrait" role="img" aria-label="Portrait photograph of Dale Fenwick in a dark blazer and white shirt"></div>
    </section>

    <section class="card card--back" aria-label="Card back">
      <div class="contact">
        <h1 class="contact__name">DALE FENWICK</h1>
        <p class="contact__title">REALTOR®</p>
        <div class="contact__rule"></div>
        <p class="contact__line">555.417.2093</p>
        <p class="contact__line">HomesWithDale@mailbox-demo.com</p>
        <div class="contact__rule"></div>
      </div>
      <div class="brokerage">
        <span class="brokerage__dot"></span>
        <p class="brokerage__name">Wexford Calloway<br>Home Services<br>Pemberly Estates</p>
      </div>
    </section>
  </main>
</body>
</html>
```